Business Card Design for Online Gift Business

Business card design for a new online Canadian company called "Harlow & Brine Gift Boxes" selling modern and luxurious gift boxes for every occasion. Items are sourced locally from talented socially-responsible Canadian artisans. Each gift is elegantly presented in a keepsake wood box to ensure a lasting impression.

Industry/Entity Type

E-Commerce

Contact Information for Business Card

Marla Whitcombe, Proprietor
Calgary, AB
403-555-2741
www.harlowandbrine.ca
hello@harlowandbrine.ca

Requirements
Must have
• Gifts from our best, to your best
• Please also include the symbols for Facebook and Instagram
Nice to have
• **I have attached a few samples of background colors and font colors that I like. I hope this helps in a few directions to try.

```html
<!DOCTYPE html>
<html lang="en">
<head>
<meta charset="utf-8">
<title>Harlow &amp; Brine Gift Boxes — Business Card</title>
<link href="https://fonts.googleapis.com/css2?family=PT+Sans:ital,wght@0,400;0,700;1,400&display=swap" rel="stylesheet">
<style>
  :root {
    --backdrop: #5b4b3d;
    --card-white: #ffffff;
    --card-sand: #cfc4b2;
    --tan: #b39b78;
    --slate: #737373;
    --ink: #4a4a4a;
    --rule: #d9d2c6;
  }
  * { margin: 0; padding: 0; box-sizing: border-box; }
  html, body {
    width: 1200px; height: 987px; overflow: hidden;
    background: var(--backdrop);
    font-family: "PT Sans", sans-serif;
  }
  .stage { position: relative; width: 1200px; height: 987px; }
  .card {
    position: absolute; left: 293px; width: 615px; height: 351px;
    border-radius: 18px; overflow: hidden;
  }
  .card--front { top: 130px; background: var(--card-white); }
  .card--back { top: 505px; background: var(--card-sand); }

  .brand-name {
    position: absolute; color: var(--tan); font-weight: 400;
    white-space: nowrap; line-height: 1;
  }
  .card--front .brand-name {
    left: 64px; top: 160px; font-size: 32px;
  }
  .card--back .brand-name {
    left: 0; right: 0; top: 152px; text-align: center;
    font-size: 52px; color: #6b5a45;
  }

  .divider {
    position: absolute; left: 319px; top: 107px;
    width: 1px; height: 125px; background: var(--rule);
  }
  .contact { position: absolute; left: 342px; top: 116px; color: var(--ink); }
  .contact__name { font-size: 21px; font-weight: 700; color: var(--tan); line-height: 1.1; }
  .contact__role { font-size: 16px; margin-top: 3px; }
  .contact__city { font-size: 15px; margin-top: 13px; }
  .contact__phone { font-size: 15px; margin-top: 11px; display: flex; align-items: center; gap: 5px; }
  .contact__phone svg { width: 14px; height: 14px; fill: var(--tan); }

  .web-band {
    position: absolute; left: 0; top: 304px; width: 100%; height: 32px; display: flex;
  }
  .web-band__url {
    flex: 0 0 486px; background: var(--tan); color: #fff;
    font-style: italic; font-size: 15px; letter-spacing: 3.2px;
    display: flex; align-items: center; justify-content: flex-end; padding-right: 56px;
  }
  .web-band__end { flex: 1; background: var(--slate); }
</style>
</head>
<body>
<main class="stage">
  <section class="card card--front" aria-label="Business card front">
    <div class="brand-name">Harlow &amp; Brine</div>
    <div class="divider"></div>
    <div class="contact">
      <p class="contact__name">Marla Whitcombe</p>
      <p class="contact__role">Proprietor</p>
      <p class="contact__city">Calgary, AB</p>
      <p class="contact__phone">
        <svg viewBox="0 0 24 24" aria-hidden="true"><path d="M6.6 10.8a15.1 15.1 0 0 0 6.6 6.6l2.2-2.2c.3-.3.7-.4 1-.2 1.1.4 2.3.6 3.6.6.6 0 1 .4 1 1V20c0 .6-.4 1-1 1C10.6 21 3 13.4 3 4c0-.6.4-1 1-1h3.5c.6 0 1 .4 1 1 0 1.3.2 2.5.6 3.6.1.3 0 .7-.2 1z"/></svg>
        403-555-2741
      </p>
    </div>
    <div class="web-band">
      <div class="web-band__url">www.harlowandbrine.ca</div>
      <div class="web-band__end"></div>
    </div>
  </section>

  <section class="card card--back" aria-label="Business card back">
    <div class="brand-name">Harlow &amp; Brine</div>
  </section>
</main>
</body>
</html>
```